Business Card Design Project

Business Card design based on logo.
Updates

I need business card, letterhead, envelope, and if possible, Powerpoint slide template.

On front of business card: Just logo- and  my name and title:  Harriet Lindqvist, Principal

On reverse-logo and the rest of the contact info:

4871 Quarry Lane
Davis, CA 95618
650-318-2764
hl@brackenstudyworks.example

On letterhead-Just logo at top, at bottom  the rest-very small along the bottom

On PPT slide-just the logo.

I also want to try a few other colors-I like lime/dark grey (not black) but would like to try Sienna, maybe also indigo or bright blue-green.

I forgot to add-

On the business card-switch to vertical on reverse side and put:

Reverse side-switch to vertical and list:

Harriet Lindqvist
Principal
Bracken Study Works, LLC

650-318-2764

4871 Quarry Lane
Davis, CA 95618

Harriet Lindqvist
Principal

650-318-2764

4871 Quarry Lane
Davis, CA 95618

I have another project at the same time-for Stationery. Feel free to submit to that one also.

That one includes letterhead, envelope, PPT slide, folder cover sheet-HL

Industry/Entity Type

Business

Requirements
Must have
• Must use logo-preferably lime green version-with gray, not black or just 2-tone -logo on colored background.

```html
<!DOCTYPE html>
<html lang="en">
<head>
<meta charset="utf-8">
<title>Bracken Study Works – Business Card</title>
<link href="https://fonts.googleapis.com/css2?family=Source+Sans+3:wght@400;600&display=swap" rel="stylesheet">
<style>
  :root {
    --backdrop: #2b2b2b;
    --card: #ffffff;
    --ink: #3f3f3f;
    --lime: #8cb82b;
    --rule: #c9c9c9;
  }
  * { margin: 0; padding: 0; box-sizing: border-box; }
  html, body {
    width: 1200px;
    height: 722px;
    overflow: hidden;
    background: var(--backdrop);
    font-family: "Source Sans 3", sans-serif;
    color: var(--ink);
  }
  .canvas { position: relative; width: 1200px; height: 722px; }
  .card {
    position: absolute;
    width: 525px;
    height: 300px;
    background: var(--card);
    border-radius: 14px;
  }
  .card--front { left: 60px; top: 211px; }
  .card--back { left: 613px; top: 212px; }

  .brand {
    position: absolute;
    left: 0; right: 0;
    display: flex;
    flex-direction: column;
    align-items: center;
  }
  .card--front .brand { top: 52px; }
  .card--back .brand { top: 40px; }
  .brand__mark {
    width: 44px; height: 44px;
    border-radius: 50%;
    background: var(--lime);
    margin-bottom: 18px;
  }
  .brand__name {
    font-size: 31px;
    font-weight: 400;
    letter-spacing: 3px;
    color: var(--ink);
    text-transform: uppercase;
    white-space: nowrap;
  }

  .website {
    position: absolute;
    left: 0; right: 0;
    top: 213px;
    text-align: center;
    font-size: 14px;
    letter-spacing: 1.2px;
    color: var(--ink);
  }
  .website__domain { color: var(--lime); }

  .contact {
    position: absolute;
    top: 217px;
    left: 0; right: 0;
    display: flex;
    justify-content: center;
    font-size: 13.5px;
    line-height: 22px;
  }
  .contact__identity { text-align: right; padding-right: 14px; }
  .contact__name { color: var(--lime); font-weight: 600; font-size: 16px; }
  .contact__title { color: var(--ink); }
  .contact__lines {
    border-left: 1px solid var(--rule);
    padding-left: 8px;
  }
  .contact__line { display: flex; align-items: center; gap: 8px; }
  .contact__icon { width: 11px; height: 11px; fill: var(--lime); flex: none; }
</style>
</head>
<body>
<main class="canvas">
  <section class="card card--front" aria-label="Business card front">
    <div class="brand">
      <span class="brand__mark"></span>
      <span class="brand__name">Bracken Study Works</span>
    </div>
    <p class="website">www.<span class="website__domain">brackenstudyworks</span>.example</p>
  </section>

  <section class="card card--back" aria-label="Business card back">
    <div class="brand">
      <span class="brand__mark"></span>
      <span class="brand__name">Bracken Study Works</span>
    </div>
    <div class="contact">
      <div class="contact__identity">
        <div><span class="contact__name">Harriet Lindqvist,</span> <span class="contact__title">Principal</span></div>
        <div>4871 Quarry Lane Davis, CA 95618</div>
      </div>
      <div class="contact__lines">
        <div class="contact__line">
          <svg class="contact__icon" viewBox="0 0 24 24" aria-hidden="true"><path d="M6.6 10.8a15 15 0 0 0 6.6 6.6l2.2-2.2a1 1 0 0 1 1-.25 11.4 11.4 0 0 0 3.6.57 1 1 0 0 1 1 1V20a1 1 0 0 1-1 1A17 17 0 0 1 3 4a1 1 0 0 1 1-1h3.5a1 1 0 0 1 1 1c0 1.25.2 2.45.57 3.6a1 1 0 0 1-.25 1z"/></svg>
          <span>650-318-2764</span>
        </div>
        <div class="contact__line">
          <svg class="contact__icon" viewBox="0 0 24 24" aria-hidden="true"><path d="M2 5h20v14H2z M3 6l9 7 9-7" fill="none" stroke="#8cb82b" stroke-width="2.4"/></svg>
          <span>hl@brackenstudyworks.example</span>
        </div>
      </div>
    </div>
  </section>
</main>
</body>
</html>
```